eCommerce website for a DIY shop & communal center

We need a website for a business called The Maple Bench. The Maple Bench is both a shop and communal establishment where people with shared interests, especially in DIY (Do It Yourself) and crafting, can gather to shop for & work on projects while sharing ideas, equipment, supplies and knowledge. The shop is both brick & motor and online. The physical communal space provides workstations, equipment, tools and supplies and expertise for DIY lovers to create their projects.

Target Market(s)

Middle & upper class DIY enthusiasts, creative hobbyists, budding artists & small business owners

Industry/Entity Type

DIY, Arts & Crafts

Coding

Coded - Design and coding required

Number of Pages Required

5+ page

Requirements
Must have
• Menus to include 1. home page (with about us, operating hours, contacts, location, meet the team); 2. Bench activities (how to DIY at the Bench, booking, equipment & tools, house rules); 3. Bench events (events in the Bench, offsite events); 4. Resources (FAQs, tutorials, blogs, eBooks) and 5. Online shop
Nice to have
• Branding guidelines eg logo colours (see attachment) to influence design. Tillpost shop. Booking feature for activities & events at the Bench.

```html
<!DOCTYPE html>
<html lang="en">
<head>
<meta charset="utf-8">
<title>The Maple Bench – Online Store</title>
<link href="https://fonts.googleapis.com/css2?family=Roboto:wght@400;500;700;900&family=Lora:wght@500&display=swap" rel="stylesheet">
<style>
:root{
  --orange:#f47c3c;
  --blue:#2e9ad6;
  --pink:#ea4080;
  --ink:#1a1a1a;
  --muted:#666;
  --line:#e3e3e3;
  --gold:#f2b01e;
  --footer:#050505;
}
*{box-sizing:border-box;margin:0;padding:0}
html,body{width:1200px;height:2933px;overflow:hidden;background:#fff;font-family:'Roboto',sans-serif;color:var(--ink)}
.page{position:relative;width:1200px;height:2933px}
.abs{position:absolute}

.topbar{left:0;top:0;width:1200px;height:49px;border-bottom:1px solid var(--line)}
.phone{left:100px;top:5px;display:flex;align-items:center;gap:12px;font-size:15px}
.phone .ring{width:38px;height:38px;border:1.5px solid #999;border-radius:50%;display:flex;align-items:center;justify-content:center}
.socials-top{right:100px;top:5px;display:flex;gap:6px}
.socials-top span{width:38px;height:38px;border:1.5px solid #999;border-radius:50%;display:block}

.nav{top:64px;font-size:15.5px;font-weight:500;letter-spacing:.2px}
.hero{left:0;top:100px;width:1200px;height:296px;background:linear-gradient(100deg,#c49a66 0%,#b8885a 30%,#6c6a66 55%,#9a8f84 75%,#8a6e4e 100%)}
.hero h1{position:absolute;left:103px;top:86px;color:#fff;font-size:56px;font-weight:900;letter-spacing:.5px}
.logo{left:520px;top:0;width:160px;height:136px;background:#fff;border-radius:0 0 80px 80px;display:flex;align-items:center;justify-content:center;text-align:center;color:var(--orange);font-weight:700;font-size:22px;line-height:1.1}

.filters{top:467px;height:48px;border-radius:24px;color:#fff;font-size:15px;font-weight:700;display:flex;align-items:center;justify-content:center}
.f-all{left:268px;width:125px;background:var(--orange)}
.f-box{left:413px;width:250px;background:var(--blue)}
.f-made{left:683px;width:251px;background:var(--pink)}

.section-title{left:101px;top:580px;font-family:'Lora',serif;font-size:32px;font-weight:500}
.sort{left:924px;top:580px;width:176px;height:44px;border:1px solid var(--line);font-size:18px;color:var(--muted);padding:10px 18px}
.sort svg{position:absolute;right:8px;top:18px}

.card{width:321px}
.card .photo{width:321px;height:331px}
.card .title{margin-top:22px;display:flex;justify-content:space-between;align-items:center;font-size:18px;font-weight:500;padding:0 2px}
.card .meta{margin-top:12px;font-size:16px;padding:0 2px;display:flex;align-items:center;gap:12px}
.stars{color:var(--gold);font-size:12px;letter-spacing:1px}
.reviews{font-size:11px;color:var(--muted)}

.pager{top:2444px;left:516px;display:flex;gap:6px}
.pager span{height:30px;min-width:30px;border:1px solid #ccc;color:#888;font-size:16px;display:flex;align-items:center;justify-content:center;padding:0 10px}
.pager .on{background:var(--orange);border-color:var(--orange);color:#fff}

.footer{left:0;top:2570px;width:1200px;height:363px;background:var(--footer);color:#fff}
.fcol{position:absolute;top:88px}
.fcol h4{font-size:17px;font-weight:700;margin-bottom:12px}
.fcol p{font-size:14.5px;line-height:28.5px}
.email{position:absolute;left:842px;top:111px;width:258px;height:41px;background:#fff;border-radius:21px;color:#333;font-size:13px;padding:12px 15px}
.subscribe{position:absolute;left:842px;top:160px;width:258px;height:42px;background:var(--orange);border-radius:21px;font-weight:700;font-size:14px;display:flex;align-items:center;justify-content:center}
.fsocial{position:absolute;left:852px;top:224px;display:flex;gap:7px}
.fsocial span{width:35px;height:35px;border-radius:50%;background:#fff;display:block}
.rule{position:absolute;left:100px;top:293px;width:1000px;height:1px;background:#2a2a2a}
.copy{position:absolute;left:0;top:313px;width:1200px;text-align:center;font-size:13px}
</style>
</head>
<body>
<div class="page">

  <header class="abs topbar">
    <div class="abs phone">
      <span class="ring"><svg width="16" height="16" viewBox="0 0 24 24"><path d="M6.6 10.8a15 15 0 0 0 6.6 6.6l2.2-2.2a1 1 0 0 1 1-.25 11 11 0 0 0 3.6.57 1 1 0 0 1 1 1V20a1 1 0 0 1-1 1A17 17 0 0 1 3 4a1 1 0 0 1 1-1h3.5a1 1 0 0 1 1 1 11 11 0 0 0 .57 3.6 1 1 0 0 1-.25 1z" fill="#999"/></svg></span>
      <span>888 - 888 - 8888</span>
    </div>
    <div class="abs socials-top" aria-label="Social links"><span></span><span></span><span></span><span></span></div>
  </header>

  <div class="abs nav" style="left:100px">HOME</div>
  <div class="abs nav" style="left:195px">BENCH ACTIVITIES</div>
  <div class="abs nav" style="left:380px">BENCH EVENTS</div>
  <div class="abs nav" style="left:704px">RESOURCES</div>
  <div class="abs nav" style="left:849px">ONLINE SHOP</div>
  <div class="abs nav" style="left:1007px">CONTACT US</div>

  <section class="abs hero" role="img" aria-label="Mitre saw on a workshop bench">
    <h1>ONLINE STORE</h1>
  </section>

  <div class="abs logo">The Maple<br>Bench</div>

  <div class="abs filters f-all">ALL</div>
  <div class="abs filters f-box">RAINY DAY BOX</div>
  <div class="abs filters f-made">MADE BY THE MAPLE BENCH</div>

  <h2 class="abs section-title">Best Selling</h2>
  <div class="abs sort">Best Selling<svg width="12" height="7"><path d="M0 0h12L6 7z" fill="#222"/></svg></div>

  <!-- product grid -->
  <div class="abs card" style="left:100px;top:659px"><div class="photo" role="img" aria-label="Wooden play kitchen unit" style="background:linear-gradient(160deg,#c9c3b6,#d8c6a4)"></div><div class="title">Finibus Bonorum et Malorum<svg width="18" height="16" viewBox="0 0 24 22"><path d="M12 20S2 13.5 2 7.5A5 5 0 0 1 12 5a5 5 0 0 1 10 2.5C22 13.5 12 20 12 20z" fill="none" stroke="#222" stroke-width="1.8"/></svg></div><div class="meta">From $40.00<span class="stars">★★★★★</span><span class="reviews">(200+reviewer)</span></div></div>
  <div class="abs card" style="left:440px;top:659px"><div class="photo" role="img" aria-label="Painted canvas of a boat at sea" style="background:linear-gradient(160deg,#3f6fc0,#2a55a8 60%,#b9a98a)"></div><div class="title">Finibus Bonorum et Malorum<svg width="18" height="16" viewBox="0 0 24 22"><path d="M12 20S2 13.5 2 7.5A5 5 0 0 1 12 5a5 5 0 0 1 10 2.5C22 13.5 12 20 12 20z" fill="none" stroke="#222" stroke-width="1.8"/></svg></div><div class="meta">From $40.00<span class="stars">★★★★★</span><span class="reviews">(200+reviewer)</span></div></div>
  <div class="abs card" style="left:780px;top:659px"><div class="photo" role="img" aria-label="Painted wood slice with sunset scene" style="background:radial-gradient(circle at 50% 50%,#f0b440 0%,#e98a2c 35%,#1d1d20 62%)"></div><div class="title">Finibus Bonorum et Malorum<svg width="18" height="16" viewBox="0 0 24 22"><path d="M12 20S2 13.5 2 7.5A5 5 0 0 1 12 5a5 5 0 0 1 10 2.5C22 13.5 12 20 12 20z" fill="none" stroke="#222" stroke-width="1.8"/></svg></div><div class="meta">From $40.00<span class="stars">★★★★★</span><span class="reviews">(200+reviewer)</span></div></div>

  <div class="abs card" style="left:100px;top:1099px"><div class="photo" role="img" aria-label="Wooden dartboard cabinet" style="background:linear-gradient(180deg,#3a3a32,#e4d7c2 30%,#d9c8ad 80%,#6a3a2a)"></div><div class="title">Finibus Bonorum et Malorum<svg width="18" height="16" viewBox="0 0 24 22"><path d="M12 20S2 13.5 2 7.5A5 5 0 0 1 12 5a5 5 0 0 1 10 2.5C22 13.5 12 20 12 20z" fill="none" stroke="#222" stroke-width="1.8"/></svg></div><div class="meta">From $40.00<span class="stars">★★★★★</span><span class="reviews">(200+reviewer)</span></div></div>
  <div class="abs card" style="left:440px;top:1099px"><div class="photo" role="img" aria-label="Glowing slatted wooden lamps" style="background:linear-gradient(90deg,#5a2a0e,#d97a1c 30%,#3a1a08 50%,#e08a28 75%,#4a220a)"></div><div class="title">Finibus Bonorum et Malorum<svg width="18" height="16" viewBox="0 0 24 22"><path d="M12 20S2 13.5 2 7.5A5 5 0 0 1 12 5a5 5 0 0 1 10 2.5C22 13.5 12 20 12 20z" fill="none" stroke="#222" stroke-width="1.8"/></svg></div><div class="meta">From $40.00<span class="stars">★★★★★</span><span class="reviews">(200+reviewer)</span></div></div>
  <div class="abs card" style="left:780px;top:1099px"><div class="photo" role="img" aria-label="Hanging painted tiles on a wall" style="background:linear-gradient(160deg,#e6e0cf,#d8d1bd)"></div><div class="title">Finibus Bonorum et Malorum<svg width="18" height="16" viewBox="0 0 24 22"><path d="M12 20S2 13.5 2 7.5A5 5 0 0 1 12 5a5 5 0 0 1 10 2.5C22 13.5 12 20 12 20z" fill="none" stroke="#222" stroke-width="1.8"/></svg></div><div class="meta">From $40.00<span class="stars">★★★★★</span><span class="reviews">(200+reviewer)</span></div></div>

  <div class="abs card" style="left:100px;top:1535px"><div class="photo" role="img" aria-label="Blue slatted wall planter with plants" style="background:linear-gradient(90deg,#eef0f0,#4f6f90 45%,#3c5a3a 70%,#eef0f0)"></div><div class="title">Finibus Bonorum et Malorum<svg width="18" height="16" viewBox="0 0 24 22"><path d="M12 20S2 13.5 2 7.5A5 5 0 0 1 12 5a5 5 0 0 1 10 2.5C22 13.5 12 20 12 20z" fill="none" stroke="#222" stroke-width="1.8"/></svg></div><div class="meta">From $40.00<span class="stars">★★★★★</span><span class="reviews">(200+reviewer)</span></div></div>
  <div class="abs card" style="left:440px;top:1535px"><div class="photo" role="img" aria-label="Framed sports jersey" style="background:linear-gradient(160deg,#3d5a30,#5a3a28 25%,#1c1c22 50%,#5a3a28 75%,#3d5a30)"></div><div class="title">Finibus Bonorum et Malorum<svg width="18" height="16" viewBox="0 0 24 22"><path d="M12 20S2 13.5 2 7.5A5 5 0 0 1 12 5a5 5 0 0 1 10 2.5C22 13.5 12 20 12 20z" fill="none" stroke="#222" stroke-width="1.8"/></svg></div><div class="meta">From $40.00<span class="stars">★★★★★</span><span class="reviews">(200+reviewer)</span></div></div>
  <div class="abs card" style="left:780px;top:1535px"><div class="photo" role="img" aria-label="Wooden chicken coop with straw" style="background:linear-gradient(170deg,#cdd0c8,#d4a868 35%,#c08850 80%,#e6d3b4)"></div><div class="title">Finibus Bonorum et Malorum<svg width="18" height="16" viewBox="0 0 24 22"><path d="M12 20S2 13.5 2 7.5A5 5 0 0 1 12 5a5 5 0 0 1 10 2.5C22 13.5 12 20 12 20z" fill="none" stroke="#222" stroke-width="1.8"/></svg></div><div class="meta">From $40.00<span class="stars">★★★★★</span><span class="reviews">(200+reviewer)</span></div></div>

  <div class="abs card" style="left:100px;top:1975px"><div class="photo" role="img" aria-label="Children's wooden play kitchen outdoors" style="background:linear-gradient(180deg,#4a3a2c,#d9c9ab 25%,#ece8e0 70%,#8a4a30)"></div><div class="title">Finibus Bonorum et Malorum<svg width="18" height="16" viewBox="0 0 24 22"><path d="M12 20S2 13.5 2 7.5A5 5 0 0 1 12 5a5 5 0 0 1 10 2.5C22 13.5 12 20 12 20z" fill="none" stroke="#222" stroke-width="1.8"/></svg></div><div class="meta">From $40.00<span class="stars">★★★★★</span><span class="reviews">(200+reviewer)</span></div></div>
  <div class="abs card" style="left:440px;top:1975px"><div class="photo" role="img" aria-label="Wooden dining table with benches in a garden" style="background:linear-gradient(180deg,#e8e6dc,#6a7a4a 30%,#8a8a80 60%,#6a6058)"></div><div class="title">Finibus Bonorum et Malorum<svg width="18" height="16" viewBox="0 0 24 22"><path d="M12 20S2 13.5 2 7.5A5 5 0 0 1 12 5a5 5 0 0 1 10 2.5C22 13.5 12 20 12 20z" fill="none" stroke="#222" stroke-width="1.8"/></svg></div><div class="meta">From $40.00<span class="stars">★★★★★</span><span class="reviews">(200+reviewer)</span></div></div>
  <div class="abs card" style="left:780px;top:1975px"><div class="photo" role="img" aria-label="Wooden slatted crate held in a garden" style="background:linear-gradient(180deg,#5a6a40,#8a7a5a 35%,#d8cfae 55%,#9a5a3a)"></div><div class="title">Finibus Bonorum et Malorum<svg width="18" height="16" viewBox="0 0 24 22"><path d="M12 20S2 13.5 2 7.5A5 5 0 0 1 12 5a5 5 0 0 1 10 2.5C22 13.5 12 20 12 20z" fill="none" stroke="#222" stroke-width="1.8"/></svg></div><div class="meta">From $40.00<span class="stars">★★★★★</span><span class="reviews">(200+reviewer)</span></div></div>

  <nav class="abs pager"><span class="on">1</span><span>2</span><span>3</span><span>Next</span></nav>

  <footer class="abs footer">
    <div class="fcol" style="left:101px"><h4>ABOUT</h4><p>Our Story<br>Press<br>Locations<br>Blog<br>Contact Us</p></div>
    <div class="fcol" style="left:237px"><h4>OUR OFFERING</h4><p>Projects<br>Paint Room<br>Parties<br>Classes</p></div>
    <div class="fcol" style="left:421px"><h4>OTHER</h4><p>Franchise<br>Gift Cards<br>FAQ<br>Refund Policy</p></div>
    <div class="fcol" style="left:572px"><h4>CONTACT US</h4><p>1234 Somestreet Anywhere USA<br>21212<br>888 - 888 - 8888<br>info@maplebench.com</p></div>
    <div class="fcol" style="left:842px"><h4>GET UPDATES &amp; PROMOS</h4></div>
    <div class="email">Email Address</div>
    <div class="subscribe">SUBSCRIBE</div>
    <div class="fsocial" aria-label="Social links"><span></span><span></span><span></span><span></span></div>
    <div class="rule"></div>
    <div class="copy">Copyright © 2021 The Maple Bench. All rights reserved.</div>
  </footer>

</div>
</body>
</html>
```